A website for Kovadrel Limited

We need a new and modern website for our company. We are engineering consultants and contractors (EPC) in the oil and gas industry and building services industry.
What we do:
Engineering, procurement, construction
Automation (safety and process)
Non-destructive testing
Training
We have an existing website and the content can be referred from there since we are remaking the website
For more information visit Kovadrel Limited Kenya

```html
<!DOCTYPE html>
<html lang="en">
<head>
<meta charset="utf-8">
<title>Kovadrel Limited</title>
<link href="https://fonts.googleapis.com/css2?family=Poppins:wght@500;600;700&display=swap" rel="stylesheet">
<style>
:root{
  --rust:#a5402b;
  --rust-dark:#8e3422;
  --orange:#e0683c;
  --ink:#1a1a1a;
  --footer:#140a07;
  --white:#ffffff;
  --grey-line:#e6e2de;
}
*{margin:0;padding:0;box-sizing:border-box}
html,body{width:1200px;height:3234px;overflow:hidden;background:var(--white)}
body{position:relative;font-family:'Poppins',sans-serif;color:var(--ink)}
.abs{position:absolute}
.caps{text-transform:uppercase;font-weight:600}

/* header */
.site-header{left:0;top:0;width:1200px;height:82px;background:var(--white)}
.brand{display:flex;align-items:center;gap:8px}
.brand-dot{width:62px;height:62px;border-radius:50%;background:var(--rust);flex:none}
.brand-name{font-weight:500;font-size:19px;line-height:24px;color:#b97b62;letter-spacing:.5px}
.header-brand{left:117px;top:10px}
.menu-icon{left:1004px;top:24px;width:38px;height:30px}
.menu-icon span{display:block;height:4px;background:var(--rust);border-radius:2px;margin-bottom:8px}

/* hero */
.hero{left:0;top:82px;width:1200px;height:544px;overflow:hidden}
.hero-photo{left:0;top:0;width:1200px;height:544px;background:linear-gradient(120deg,#8a5a3c 0%,#a9764f 40%,#7a5036 70%,#b59a7a 100%)}
.hero-title{left:100px;top:158px;width:400px;text-align:center;font-weight:700;font-size:69px;line-height:76px;color:var(--white)}

/* history */
.history-title{left:115px;top:752px;font-size:45px;font-weight:700;color:var(--rust)}
.body-text{font-size:15.5px;line-height:30px;text-transform:uppercase;font-weight:600}
.history-text{left:115px;top:818px;width:420px;color:var(--ink)}
.btn{display:flex;align-items:center;justify-content:center;font-weight:600;font-size:19px;text-transform:uppercase;letter-spacing:.5px}
.btn-rust{background:var(--rust);color:var(--white)}
.btn-white{background:var(--white);color:var(--rust)}
.photo-circle{border-radius:50%;border:7px solid var(--white);box-shadow:0 4px 18px rgba(0,0,0,.25)}

/* who */
.who-title{left:639px;top:1276px;font-size:45px;font-weight:700;color:var(--white)}
.who-text{left:641px;top:1350px;width:460px;color:var(--white)}

/* what we do */
.what-title{left:428px;top:1850px;width:400px;text-align:center;font-size:45px;font-weight:700;color:var(--rust)}
.service{width:246px;height:246px;border-radius:50%;display:flex;align-items:center;justify-content:center;text-align:center;color:var(--white);font-size:13px;line-height:30px;font-weight:600;text-transform:uppercase;padding:0 14px}
.service.rim-rust{border:7px solid var(--rust)}
.service.rim-white{border:7px solid var(--white)}

/* vision */
.vision-title{left:0;top:2490px;width:1200px;text-align:center;font-size:45px;font-weight:700;color:var(--white)}
.vision-text{left:0;top:2574px;width:1200px;text-align:center;font-size:15.5px;font-weight:600;text-transform:uppercase;color:var(--white)}

/* footer */
.foot-head{font-size:18px;font-weight:600;color:var(--white);text-transform:uppercase}
.foot-list{list-style:none;font-size:15px;line-height:30px;font-weight:600;color:var(--white);text-transform:uppercase}
.contact{display:flex;gap:18px;align-items:flex-start;color:var(--white);font-size:15px;line-height:30px;font-weight:600;text-transform:uppercase}
.contact svg{flex:none;margin-top:6px}
.footer-brand .brand-name{color:var(--white)}
.footer-brand .brand-dot{background:var(--white);width:58px;height:58px}
.copyright{left:0;top:3192px;width:1200px;text-align:center;color:var(--white);font-size:13.5px;font-weight:600;text-transform:uppercase}
</style>
</head>
<body>

<header class="abs site-header">
  <div class="abs brand header-brand">
    <div class="brand-dot"></div>
    <div class="brand-name">KOVADREL<br>LIMITED</div>
  </div>
  <div class="abs menu-icon" aria-label="Menu"><span></span><span></span><span></span></div>
</header>

<section class="abs hero">
  <div class="abs hero-photo" role="img" aria-label="Engineers in hard hats reviewing construction plans on a wooden table"></div>
  <svg class="abs" style="left:0;top:0" width="1200" height="544" aria-hidden="true">
    <path d="M0 0 H440 C520 120 520 420 440 544 H0 Z" fill="#b8562f" opacity=".82"/>
    <path d="M0 10 C140 90 170 300 60 450 L0 480" fill="none" stroke="#f3cdb8" stroke-width="1.5"/>
  </svg>
  <h1 class="abs hero-title">KOVADREL LIMITED</h1>
</section>

<section class="abs" style="left:0;top:626px;width:1200px;height:566px">
  <svg class="abs" style="left:0;top:0" width="1200" height="566" aria-hidden="true">
    <polygon points="772,0 1200,0 1200,566 832,566 602,303" fill="var(--rust)"/>
    <polyline points="1200,44 1060,282 1200,448" fill="none" stroke="#e4a18d" stroke-width="1.5"/>
  </svg>
</section>
<h2 class="abs history-title">HISTORY</h2>
<p class="abs body-text history-text">Kovadrel was incorporated in 2010 with the huge potential of the LPG and petroleum market in Eastern and Central Africa in mind. We have provided and continue to provide the LPG and petroleum technical industry with innovative and cost-effective services.</p>
<div class="abs btn btn-rust" style="left:117px;top:1025px;width:172px;height:51px">Read More</div>
<div class="abs photo-circle" style="left:618px;top:696px;width:426px;height:426px;background:radial-gradient(circle at 70% 60%,#a9c3ea 0%,#3c4f86 25%,#1d2545 60%,#131829 100%)" role="img" aria-label="Welder at work with sparks flying"></div>

<section class="abs" style="left:0;top:1192px;width:1200px;height:578px;background:var(--rust)">
  <div class="abs" style="left:0;top:0;width:1200px;height:578px;background:linear-gradient(135deg,#c6826a,#d6a38d 50%,#c98a6b)" role="img" aria-label="Team of engineers working together at a desk"></div>
  <svg class="abs" style="left:0;top:0" width="1200" height="578" aria-hidden="true">
    <polygon points="357,0 1200,0 1200,578 289,578" fill="var(--rust)"/>
    <polygon points="0,0 357,0 289,578 0,578" fill="#c98c77" opacity=".35"/>
    <polyline points="1200,300 1060,578" fill="none" stroke="#e4a18d" stroke-width="1.5"/>
    <polyline points="0,40 120,220 0,460" fill="none" stroke="#f3d4c6" stroke-width="1.5"/>
  </svg>
</section>
<div class="abs photo-circle" style="left:132px;top:1267px;width:432px;height:432px;background:linear-gradient(135deg,#d9dbe0 0%,#5b5f68 40%,#8c1e1e 55%,#2a2d33 75%,#111 100%)" role="img" aria-label="Industrial plant with steel pipework and red conveyor"></div>
<h2 class="abs who-title">WHO WE ARE</h2>
<p class="abs body-text who-text">Kovadrel undertakes design, supply, installation and commissioning of LPG and petroleum systems including LPG reticulated systems (piped gas). We also do LPG tank revalidation and recertification. Our clients include: oil companies (both multinationals and local), government agencies, manufacturing companies, agricultural institutions, and the building services industry.</p>
<div class="abs btn btn-white" style="left:639px;top:1619px;width:172px;height:51px">Read More</div>

<section class="abs" style="left:0;top:1770px;width:1200px;height:651px">
  <svg class="abs" style="left:0;top:0" width="1200" height="651" aria-hidden="true">
    <line x1="0" y1="0" x2="1200" y2="0" stroke="var(--grey-line)" stroke-width="2"/>
    <polygon points="970,0 1200,0 1200,651 1033,651 803,326" fill="var(--rust)"/>
    <polyline points="1200,0 1018,093 1200,330" fill="none" stroke="#e4a18d" stroke-width="1.5"/>
    <polyline points="1200,380 1125,505 1200,620" fill="none" stroke="#e4a18d" stroke-width="1.5"/>
  </svg>
</section>
<h2 class="abs what-title">WHAT WE DO</h2>
<div class="abs service rim-rust" style="left:3px;top:1975px;background:linear-gradient(160deg,#5a4a3a,#2b2a2e 60%,#4a3a1e)" role="img" aria-label="Engineering plant machinery">Engineering, procurement, construction</div>
<div class="abs service rim-rust" style="left:280px;top:1975px;background:linear-gradient(180deg,#4a5266,#3a3448 55%,#5b3a2c)" role="img" aria-label="Refinery silhouette at dusk">Automation<br>(safety and process)</div>
<div class="abs service rim-rust" style="left:558px;top:1975px;background:linear-gradient(180deg,#23306a 0%,#2c3b7a 45%,#c9a820 60%,#7a6a1a 100%)" role="img" aria-label="Row of yellow gas cylinders">Non-destructive testing</div>
<div class="abs service rim-white" style="left:837px;top:1975px;background:linear-gradient(180deg,#8a8e92,#6a6e62 50%,#8a8a2a)" role="img" aria-label="Trainees in safety vests attending a class">Training</div>

<section class="abs" style="left:0;top:2421px;width:1200px;height:353px;background:linear-gradient(120deg,#b4553a,#a9482f 50%,#b65a3c)" role="img" aria-label="Engineering team in a meeting">
  <svg class="abs" style="left:0;top:0" width="1200" height="353" aria-hidden="true">
    <polyline points="60,0 88,35 0,150" fill="none" stroke="#e4a18d" stroke-width="1.5"/>
    <polyline points="1200,70 1160,150" fill="none" stroke="#e4a18d" stroke-width="1.5"/>
  </svg>
</section>
<h2 class="abs vision-title">OUR VISION</h2>
<p class="abs vision-text">To be a world class provider of petroleum technical expertise.</p>
<div class="abs btn btn-white" style="left:512px;top:2632px;width:173px;height:51px">Read More</div>

<footer class="abs" style="left:0;top:2774px;width:1200px;height:460px;background:var(--rust)">
  <svg class="abs" style="left:0;top:0" width="1200" height="460" aria-hidden="true">
    <polyline points="0,0 165,80 0,290" fill="none" stroke="#e4a18d" stroke-width="1.5"/>
    <polygon points="238,0 1200,0 1200,460 200,460 245,414 376,238 260,50" fill="var(--footer)"/>
    <polygon points="260,50 285,50 400,238 258,438 232,438 362,238" fill="var(--orange)"/>
  </svg>
</footer>
<div class="abs brand footer-brand" style="left:134px;top:2946px">
  <div class="brand-dot"></div>
  <div class="brand-name">KOVADREL<br>LIMITED</div>
</div>

<h3 class="abs foot-head" style="left:364px;top:2817px">Quick Links</h3>
<ul class="abs foot-list" style="left:366px;top:2866px">
  <li>Home</li><li>About Us</li><li>Services</li><li>Products</li><li>Our Projects</li><li>Our Clients</li><li>Where We Operate</li><li>Our Partners</li><li>Contacts</li>
</ul>

<h3 class="abs foot-head" style="left:616px;top:2817px">About</h3>
<p class="abs foot-list" style="left:616px;top:2866px;width:200px">Kovadrel's core business is engineering works (oil and gas engineering).</p>

<h3 class="abs foot-head" style="left:885px;top:2815px">Follow Us</h3>
<div class="abs contact" style="left:841px;top:2862px">
  <svg width="24" height="24" viewBox="0 0 24 24"><path d="M6.6 10.8a15 15 0 006.6 6.6l2.2-2.2a1 1 0 011-.25 11.4 11.4 0 003.6.57 1 1 0 011 1V20a1 1 0 01-1 1A17 17 0 013 4a1 1 0 011-1h3.5a1 1 0 011 1c0 1.25.2 2.45.57 3.57a1 1 0 01-.25 1z" fill="#fff"/></svg>
  <span>+254 700 314 552 |<br>+254 700 428 917</span>
</div>
<div class="abs contact" style="left:838px;top:2952px">
  <svg width="26" height="20" viewBox="0 0 26 20"><rect x="1" y="1" width="24" height="18" rx="2" fill="#fff"/><path d="M2 3l11 8 11-8" fill="none" stroke="var(--footer)" stroke-width="2"/></svg>
  <span>info@kovadrel.example</span>
</div>
<div class="abs contact" style="left:843px;top:3012px">
  <svg width="20" height="26" viewBox="0 0 20 26"><path d="M10 1a8 8 0 00-8 8c0 6 8 16 8 16s8-10 8-16a8 8 0 00-8-8z" fill="#fff"/><circle cx="10" cy="9" r="3" fill="var(--footer)"/></svg>
  <span>Halden Court, Suite B21,<br>Lantern Road</span>
</div>

<p class="abs copyright">Copyright © 2023 Kovadrel Limited all rights reserved.</p>

</body>
</html>
```